Business card design for holistic health care clinic

We need a double-sided business card design for our holistic health care clinic that integrates our logo design and also its color scheme. My business is called Valmira. It is an integrative medicine clinic. You have already done the logo for me. Please ensure an elegant and upscale design that is not cluttered, but still has all the necessary information (please see below for details).

Target Market(s)

Wellness, fitness, rehabilitation for educated, well-traveled open-minded clients who are focused on natural, organic, balanced and preventive healthcare and lifestyle.

Industry/Entity Type

Medical

Contact Information for Business Card

Modern, clean.

Number of Pages Required

1 page

Font styles to use
Serif
Sans Serif

Colors

Designer to choose colors to be used in the design.

Requirements
Must have
• Logo on one side, all other information on the other side.
• Other information should include:
• Tobias Wrenfeld - DOE, CPT, LMT
• 4100 East Marrow Drive
• Austin, TX 78119
• 512 555 0148
• 818 555 0192
• info@ValmiraHealth.example
• t.wrenfeld@ValmiraHealth.example
Nice to have
• Darker background on front - but not totally black - shaded/dark gray.

```html
<!DOCTYPE html>
<html lang="en">
<head>
<meta charset="UTF-8">
<title>Valmira Business Card</title>
<link href="https://fonts.googleapis.com/css2?family=Nunito:wght@700;800&family=Roboto:ital,wght@0,400;0,500;1,500&family=Roboto+Condensed:wght@700&display=swap" rel="stylesheet">
<style>
  :root {
    --backdrop: #5a4a3a;
    --card-dark: #262626;
    --card-dark-edge: #1f1f1f;
    --brand-blue: #0a8cc6;
    --brand-blue-text: #1b8fcb;
    --silver: #a8a8a8;
    --faint-mark: #294556;
    --white: #ffffff;
  }
  * { margin: 0; padding: 0; box-sizing: border-box; }
  html, body { width: 1200px; height: 960px; overflow: hidden; }
  body { background: var(--backdrop); position: relative; font-family: "Roboto", Arial, sans-serif; }

  .card {
    position: absolute;
    width: 600px;
    height: 342px;
    border-radius: 22px;
    overflow: hidden;
    background: var(--card-dark);
    box-shadow: 0 3px 6px rgba(0,0,0,0.45);
  }
  .card--front { left: 314px; top: 114px; }
  .card--back { left: 311px; top: 472px; background: linear-gradient(160deg, #2a2a2a, var(--card-dark-edge)); }

  .card__shapes { position: absolute; inset: 0; }

  .wordmark {
    position: absolute;
    font-family: "Nunito", Arial, sans-serif;
    font-weight: 800;
    color: var(--brand-blue-text);
    letter-spacing: 1px;
    line-height: 1;
  }
  .wordmark__dot {
    position: absolute;
    border-radius: 50%;
    background: var(--brand-blue-text);
  }
  .descriptor {
    position: absolute;
    font-family: "Nunito", Arial, sans-serif;
    font-weight: 700;
    color: var(--brand-blue-text);
    white-space: nowrap;
  }

  .card--front .wordmark { left: 33px; top: 82px; font-size: 52px; }
  .card--front .wordmark__dot { left: 110px; top: 52px; width: 22px; height: 22px; }
  .card--front .descriptor { left: 36px; top: 129px; font-size: 15.5px; }

  .contact-list {
    position: absolute;
    left: 34px;
    top: 242px;
    list-style: none;
    color: var(--white);
    font-size: 14.5px;
  }
  .contact-list li { display: flex; align-items: center; height: 19px; }
  .contact-list svg { width: 14px; height: 14px; margin-right: 9px; fill: var(--white); }

  .person {
    position: absolute;
    right: 40px;
    top: 234px;
    text-align: right;
    color: var(--white);
  }
  .person__name { font-family: "Roboto Condensed", Arial, sans-serif; font-weight: 700; font-size: 21px; line-height: 1.1; }
  .person__credentials { font-family: "Roboto Condensed", Arial, sans-serif; font-weight: 700; font-size: 11px; margin-bottom: 9px; }
  .person__address { font-size: 14.5px; line-height: 19px; font-style: normal; }

  .card--back .wordmark { left: 72px; top: 223px; font-size: 44px; }
  .card--back .wordmark__dot { left: 131px; top: 198px; width: 18px; height: 18px; }
  .card--back .descriptor { left: 76px; top: 263px; font-size: 13px; }
  .slogan {
    position: absolute;
    left: 72px;
    top: 282px;
    color: var(--white);
    font-style: italic;
    font-weight: 500;
    font-size: 16px;
    white-space: nowrap;
  }
  .brand-mark-faint {
    position: absolute;
    left: 300px;
    top: 40px;
    width: 330px;
    height: 302px;
  }
</style>
</head>
<body>

<section class="card card--front" aria-label="Business card front">
  <svg class="card__shapes" viewBox="0 0 600 342" aria-hidden="true">
    <path d="M0 204 L330 204 L322 220 L0 220 Z" fill="var(--silver)"/>
    <path d="M0 221 L320 221 C332 221 336 210 342 200 C348 190 354 187 366 187 L600 187 L600 342 L0 342 Z" fill="var(--brand-blue)"/>
  </svg>

  <span class="wordmark__dot" aria-hidden="true"></span>
  <div class="wordmark">VALMIRA</div>
  <div class="descriptor">Integrative Holistic Medicine</div>

  <ul class="contact-list">
    <li>
      <svg viewBox="0 0 24 24" aria-hidden="true"><path d="M6.6 10.8a15 15 0 0 0 6.6 6.6l2.2-2.2a1 1 0 0 1 1-.25 11.4 11.4 0 0 0 3.6.57 1 1 0 0 1 1 1V20a1 1 0 0 1-1 1A17 17 0 0 1 3 4a1 1 0 0 1 1-1h3.5a1 1 0 0 1 1 1c0 1.25.2 2.45.57 3.6a1 1 0 0 1-.25 1z"/></svg>
      512 555 0148
    </li>
    <li>
      <svg viewBox="0 0 24 24" aria-hidden="true"><path d="M7 1h10a2 2 0 0 1 2 2v18a2 2 0 0 1-2 2H7a2 2 0 0 1-2-2V3a2 2 0 0 1 2-2zm0 3v14h10V4zm5 15.5a1 1 0 1 0 0 2 1 1 0 0 0 0-2z"/></svg>
      818 555 0192
    </li>
    <li>
      <svg viewBox="0 0 24 24" aria-hidden="true"><path d="M2 5h20v14H2zm2 2v.5l8 5 8-5V7zm0 2.8V17h16V9.8l-8 5z"/></svg>
      t.wrenfeld@ValmiraHealth.example
    </li>
    <li>
      <svg viewBox="0 0 24 24" aria-hidden="true"><path d="M12 2a10 10 0 1 0 0 20 10 10 0 0 0 0-20zm-1 17.9A8 8 0 0 1 4.2 10L9 14.8V16a2 2 0 0 0 2 2zm6.9-2.5A2 2 0 0 0 16 16h-1v-3a1 1 0 0 0-1-1H8v-2h2a1 1 0 0 0 1-1V7h2a2 2 0 0 0 2-2v-.4a8 8 0 0 1 2.9 12.8z"/></svg>
      www.ValmiraHealth.example
    </li>
  </ul>

  <div class="person">
    <div class="person__name">TOBIAS WRENFELD</div>
    <div class="person__credentials">DOE, CPT, LMT</div>
    <address class="person__address">4100 East Marrow Drive<br>Austin, TX 78119</address>
  </div>
</section>

<section class="card card--back" aria-label="Business card back">
  <svg class="brand-mark-faint" viewBox="0 0 330 302" role="img" aria-label="Large faint brand emblem area">
    <circle cx="210" cy="170" r="150" fill="var(--faint-mark)"/>
  </svg>

  <span class="wordmark__dot" aria-hidden="true"></span>
  <div class="wordmark">VALMIRA</div>
  <div class="descriptor">Integrative Holistic Medicine</div>
  <div class="slogan">helping the body help itself</div>
</section>

</body>
</html>
```